Ferncrest Roam Wording For Logo & Business card

I have the logo, I just need the "Ferncrest Roam" wording to go with it, and a business card design. The only thing on the business card is the website info. We provide nature connection experiences, and bolster these efforts through writing and host a platform for community around it.

I also have an idea of what it could look like (sketch), though I'm really not sure how it would come out. I am open to the best design and happy to consider original artwork. You can see what the site is about at FerncrestRoam.example.

Contact Information for Business Card

The only thing on the business card is the website info and the design. I will put other messaging on the back.

Website lettering (FerncrestRoam.example) in Montserrat

Logo Text

Ferncrest Roam (letters optional)

Font styles to use
Other font styles liked:
• montserrat

```html
<!DOCTYPE html>
<html lang="en">
<head>
<meta charset="utf-8">
<title>Ferncrest Roam — Business Card</title>
<link href="https://fonts.googleapis.com/css2?family=Montserrat:wght@300;400&display=swap" rel="stylesheet">
<style>
  :root {
    --backdrop: #2a2a2a;
    --card-light: #ffffff;
    --card-dark: #110d24;
    --ink: #231f2e;
    --accent: #f7941d;
    --text-light: #f2f0f7;
    --mark-fill: #2e2250;
    --ghost: #1b1533;
  }
  * { margin: 0; padding: 0; box-sizing: border-box; }
  html, body { width: 1200px; height: 583px; overflow: hidden; }
  body {
    background: var(--backdrop);
    font-family: "Montserrat", sans-serif;
    position: relative;
  }
  .card {
    position: absolute;
    top: 154px;
    width: 480px;
    height: 274px;
    border-radius: 38px;
    box-shadow: 0 10px 18px rgba(0,0,0,0.45);
    overflow: hidden;
  }
  .card--front { left: 94px; background: var(--card-light); }
  .card--back { left: 627px; background: var(--card-dark); }

  .brand-mark {
    position: absolute;
    border-radius: 50%;
    background: var(--mark-fill);
  }
  .card--front .brand-mark { left: 84px; top: 96px; width: 82px; height: 82px; }
  .card--back .brand-mark { left: 61px; top: 86px; width: 102px; height: 102px; }

  .brand-name {
    position: absolute;
    left: 177px;
    top: 118px;
    font-weight: 300;
    font-size: 28px;
    letter-spacing: 0.04em;
    color: var(--ink);
    text-transform: uppercase;
    white-space: nowrap;
  }
  .website {
    position: absolute;
    left: 178px;
    top: 164px;
    font-weight: 400;
    font-size: 11px;
    letter-spacing: 0.2em;
    color: var(--ink);
    white-space: nowrap;
  }
  .website__domain { color: var(--accent); }

  .divider {
    position: absolute;
    left: 178px;
    top: 87px;
    width: 2px;
    height: 100px;
    background: var(--accent);
  }
  .person-name {
    position: absolute;
    left: 190px;
    top: 92px;
    font-weight: 400;
    font-size: 20px;
    letter-spacing: 0.08em;
    color: var(--accent);
    text-transform: uppercase;
    white-space: nowrap;
  }
  .contact-list {
    position: absolute;
    left: 190px;
    top: 128px;
    list-style: none;
  }
  .contact-list li {
    display: flex;
    align-items: center;
    gap: 5px;
    height: 18px;
    font-size: 13px;
    font-weight: 300;
    color: var(--text-light);
    white-space: nowrap;
  }
  .contact-list svg { width: 10px; height: 10px; flex: none; }
  .ghost-name {
    position: absolute;
    left: 190px;
    top: 220px;
    font-weight: 300;
    font-size: 26px;
    letter-spacing: 0.04em;
    color: var(--ghost);
    text-transform: uppercase;
    white-space: nowrap;
  }
</style>
</head>
<body>
  <section class="card card--front">
    <div class="brand-mark"></div>
    <h1 class="brand-name">Ferncrest Roam</h1>
    <p class="website">www.<span class="website__domain">ferncrestroam</span>.example</p>
  </section>

  <section class="card card--back">
    <div class="brand-mark"></div>
    <div class="divider"></div>
    <h2 class="person-name">Mara Quillfield</h2>
    <ul class="contact-list">
      <li>
        <svg viewBox="0 0 10 10" aria-hidden="true"><circle cx="5" cy="5" r="5" fill="var(--accent)"/><path d="M3.2 2.6l1 1-.5.6c.4.8.9 1.3 1.7 1.7l.6-.5 1 1-.7.8C4.6 7 3 5.4 2.6 3.3z" fill="var(--card-dark)"/></svg>
        555-014-229
      </li>
      <li>
        <svg viewBox="0 0 10 10" aria-hidden="true"><circle cx="5" cy="5" r="5" fill="var(--accent)"/><circle cx="5" cy="5" r="3" fill="none" stroke="var(--card-dark)" stroke-width="0.7"/><path d="M2 5h6M5 2v6" stroke="var(--card-dark)" stroke-width="0.7"/></svg>
        info@ferncrestroam.example
      </li>
      <li>
        <svg viewBox="0 0 10 10" aria-hidden="true"><circle cx="5" cy="5" r="5" fill="var(--accent)"/><path d="M5 2.4L7.4 4.6V7.4H2.6V4.6z" fill="var(--card-dark)"/></svg>
        your address,yourcity,box 88900
      </li>
    </ul>
    <p class="ghost-name" aria-hidden="true">Ferncrest Roam</p>
  </section>
</body>
</html>
```